Hard-File Archival Services Billboard (Digitization Service) for Attorneys/Law Firms

I need a billboard design for my company "Velkor Legal Aides" that advertises our primary service: Digitization of closed client files, for law firms and attorneys. Our system works as follows: 1) We get a call about a firm that wants to digitize their archived (closed) client files (which usually find their way to file cabinets or bankers boxes), 2) We go and pick those up from the law firm, 3) We bring them to our digitization facility, scan them in, and convert them into searchable PDF/A files, and 4) We upload them on the cloud, give the client a URL to visit their files whenever they want, and we delete them when requested by the client (usually for the retention duration for Missouri's rules of professional conduct, which is 6 years). It would be really cool to see "Velkor Legal Aides" and the logo clearly on the billboard, some simple sentence relating to "Missouri's best digitizing and cloud storage service for closed client files for attorneys" (or something shorter, you get the point), with maybe a linear set of photos and arrows (as follows 1. A photo of a file cabinet opened with files hanging out of it, 2. an arrow pointing to a person scanning in documents in a big scanner (maybe with a Velkor Legal Aidez logo on it?), 3. An arrow pointing to a "secure" appearing cloud (representing cloud storage), and 4. the client sitting at a computer with an arrow pointing back to the cloud (showing the client is accessing the cloud files through the computer). Our website is www.velkorlegalaides.example if you want to glean any additional information from there. Thanks! Oh yes, I should also say the billboard dimensions (in the event you need this for photo aspect ratio) will be as follows: 14 feet tall by 48 feet wide.
Target Market(s)
Attorneys in Springfield, Missouri
Industry/Entity Type
Legal
Look and feel

```html
<!DOCTYPE html>
<html lang="en">
<head>
<meta charset="utf-8">
<title>Velkor Legal Aides Billboard</title>
<link href="https://fonts.googleapis.com/css2?family=Poppins:wght@400;500;600;700;800&display=swap" rel="stylesheet">
<style>
  :root {
    --ink: #111111;
    --paper: #ffffff;
    --canvas: #f3f3f3;
    --grey-head: #bdbdbd;
    --badge-red: #d80f1a;
    --badge-gold: #f5c400;
    --badge-gold-dark: #c99a00;
    --arrow-magenta: #c653d6;
    --arrow-teal: #3f8f8c;
    --arrow-blue: #23a2cf;
  }
  * { box-sizing: border-box; margin: 0; padding: 0; }
  html, body { width: 1107px; height: 1200px; overflow: hidden; }
  body {
    background: var(--canvas);
    font-family: "Poppins", sans-serif;
    position: relative;
  }
  .billboard {
    position: absolute;
    left: 54px; top: 454px;
    width: 1000px; height: 292px;
    background: var(--paper);
    box-shadow: 0 10px 24px rgba(0,0,0,.28);
  }
  .top-band {
    position: absolute; left: 0; top: 0;
    width: 100%; height: 92px;
    background: var(--ink);
  }
  .bottom-strip {
    position: absolute; left: 0; bottom: 0;
    width: 100%; height: 10px;
    background: var(--ink);
  }
  .headline {
    position: absolute; left: 288px; top: 20px;
    color: var(--grey-head);
    font-size: 39px; font-weight: 700; line-height: 42px;
    letter-spacing: -0.5px; white-space: nowrap;
  }
  .headline .light { font-weight: 400; }
  .subline {
    position: absolute; left: 289px; top: 60px;
    color: var(--paper);
    font-size: 17.6px; font-weight: 700; line-height: 22px;
    white-space: nowrap;
  }
  .brand-mark {
    position: absolute; left: 44px; top: 104px;
    width: 222px; height: 104px;
    display: flex; align-items: center; gap: 12px;
  }
  .brand-mark .dot {
    width: 44px; height: 44px; border-radius: 50%;
    background: var(--ink); flex: none;
  }
  .brand-mark .name {
    color: var(--ink);
    font-size: 26px; font-weight: 700; line-height: 30px;
    white-space: nowrap;
  }
  .brand-mark .name span { display: block; }
  .contact-row {
    position: absolute; left: 34px; top: 226px;
    width: 940px; height: 40px;
    display: flex; align-items: center;
    color: var(--ink); white-space: nowrap;
  }
  .company-name { font-size: 24px; font-weight: 600; width: 262px; }
  .phone, .website { display: flex; align-items: center; gap: 6px; font-weight: 500; }
  .phone { font-size: 25px; width: 284px; }
  .website { font-size: 23px; }
  .step { position: absolute; border-radius: 10px; }
  .step-cabinet { left: 278px; top: 107px; width: 114px; height: 114px;
    background: linear-gradient(135deg, #e9b8ef, #2c3b40); }
  .step-scanning { left: 459px; top: 100px; width: 128px; height: 128px;
    background: linear-gradient(135deg, #eef2f2, #7fb9b4); }
  .step-cloud { left: 660px; top: 102px; width: 86px; height: 124px;
    background: linear-gradient(135deg, #d7d7f3, #e0b16a); }
  .step-client { left: 822px; top: 112px; width: 132px; height: 116px;
    background: linear-gradient(135deg, #8fdcf6, #2aa7d7); }
  .arrows { position: absolute; left: 0; top: 0; width: 1000px; height: 292px; pointer-events: none; }
  .price-badge { position: absolute; left: 836px; top: 8px; width: 126px; height: 116px; }
  .badge-label {
    position: absolute; left: 850px; top: 22px; width: 98px;
    color: var(--paper); text-align: center;
    font-size: 6.6px; font-weight: 700; line-height: 8px;
  }
  .badge-price {
    position: absolute; left: 836px; top: 66px; width: 126px;
    text-align: center; color: var(--ink);
    font-size: 25px; font-weight: 800; line-height: 34px;
  }
</style>
</head>
<body>
  <main class="billboard">
    <div class="top-band"></div>
    <div class="bottom-strip"></div>

    <div class="brand-mark">
      <span class="dot"></span>
      <span class="name"><span>Velkor</span><span>Legal Aides</span></span>
    </div>

    <h1 class="headline">TOP MISSOURI SERVICE <span class="light">FOR</span></h1>
    <p class="subline">ATTORNEY FILE DIGITIZATION AND CLOUD STORAGE</p>

    <div class="step step-cabinet" role="img" aria-label="Illustration of an open file cabinet with a person sorting client files"></div>
    <div class="step step-scanning" role="img" aria-label="Illustration of a person scanning documents at a digitization station"></div>
    <div class="step step-cloud" role="img" aria-label="Illustration of secure cloud storage with folders and documents"></div>
    <div class="step step-client" role="img" aria-label="Illustration of a client opening a cloud file drawer to access files"></div>

    <svg class="arrows" viewBox="0 0 1000 292" aria-hidden="true">
      <path d="M396 176 Q430 192 454 172" fill="none" stroke="var(--arrow-magenta)" stroke-width="4" stroke-linecap="round"/>
      <path d="M446 165 L460 166 L454 179 Z" fill="var(--arrow-magenta)"/>
      <path d="M596 148 Q622 124 646 138" fill="none" stroke="var(--arrow-teal)" stroke-width="4" stroke-linecap="round"/>
      <path d="M638 130 L654 144 L636 147 Z" fill="var(--arrow-teal)"/>
      <path d="M814 172 Q786 186 762 172" fill="none" stroke="var(--arrow-blue)" stroke-width="4" stroke-linecap="round"/>
      <path d="M768 161 L753 167 L764 180 Z" fill="var(--arrow-blue)"/>
    </svg>

    <svg class="price-badge" viewBox="0 0 126 116" aria-hidden="true">
      <circle cx="63" cy="58" r="52" fill="var(--paper)"/>
      <circle cx="63" cy="58" r="48" fill="var(--badge-red)"/>
      <path d="M2 60 L10 60 L6 68 L10 78 L2 78 Z" fill="var(--badge-gold-dark)"/>
      <path d="M124 60 L116 60 L120 68 L116 78 L124 78 Z" fill="var(--badge-gold-dark)"/>
      <rect x="6" y="56" width="114" height="36" fill="var(--badge-gold)"/>
    </svg>
    <p class="badge-label">VELKOR<br>LEGAL AIDES<br>CLOUD SERVICES<br>(VCS)</p>
    <p class="badge-price">$20.00</p>

    <div class="contact-row">
      <span class="company-name">Velkor Legal Aides</span>
      <span class="phone">
        <svg width="18" height="18" viewBox="0 0 24 24" aria-hidden="true"><path d="M6.6 10.8a15.1 15.1 0 0 0 6.6 6.6l2.2-2.2a1 1 0 0 1 1-.25 11.4 11.4 0 0 0 3.6.57 1 1 0 0 1 1 1V20a1 1 0 0 1-1 1A17 17 0 0 1 3 4a1 1 0 0 1 1-1h3.5a1 1 0 0 1 1 1c0 1.25.2 2.45.57 3.57a1 1 0 0 1-.25 1z" fill="var(--ink)"/></svg>
        +1 (417) 555-0142
      </span>
      <span class="website">
        <svg width="18" height="18" viewBox="0 0 24 24" aria-hidden="true" fill="none" stroke="var(--ink)" stroke-width="2"><circle cx="12" cy="12" r="9"/><path d="M3 12h18M12 3c3 3.2 3 14.8 0 18M12 3c-3 3.2-3 14.8 0 18"/></svg>
        www.velkorlegalaides.example
      </span>
    </div>
  </main>
</body>
</html>
```